Q.B. Brightpath Store

The design is for eCommerce home page but I would like it to complement this site: http://www.qbbrightpathsolutions.com/ but... it should also have independence as a standalone site.

The best design will be able to effectively mix corporate with a high quality small business consumer feel. It should be completely custom design, not a template look or feel. I want the users to get the feeling that this is the place to go for buying tech for business. We sell the same products as RVK.

You can be creative as you wish, as long as the elements of a great eCommerce site are present.

I would like your 'design' to blow these away:
http://www.shopping.zl.com/
mirabelo.com
http://www.rvk.com/

Here are references:
Call to action
http://markvantage.com/us/blog/48153-seven-tips-for-designing-an-effective-ecommerce-call-to-action

Effective Ecommerce design
http://www.vexa.com/ss/7-tips-for-effective-e-commerce#0

91 points of ecommerce
http://qir.com/blog/holygrail-of-ecommerce-conversion-optimization-91-points-checklist

UPDATE 07/11/2013:

Please look at the category sample png files. I see already many people are using the main menu from qbbrightpathsolutions.com and I do not mind your creativiety, but this is an eCommerce store and people need a menu to get to the categories and/or product types. I don't want to limit anyone creativity by the png samples. I'm also not using them to show I like them in any particular way or form, just that it's needed, whether it's a button (dropdown of course) that says 'Categories' or 'Products, whether it an accordion, horizontal or vertical.

Thanks

UPDATE 07/12/2013:

Please find other use of space that has been used for About Us paragraph (if you've added it to the page). About Us should have it's own page and the purpose of the design should be to sell products (and some services as products). Please put a link or some other creative method to lead users to the About Us page.

Reason: I've raised the award, including 1st, 2nd, and 3rd place and participation payments so I will also extend 7 days. Thanks!

I've updated the product brief. Please scroll down to where it says: UPDATE 07/11/2013

Thanks!

UPDATE 07/12/2013:

Please find other use of space that has been used for About Us paragraph (if you've added it to the page).  About Us should have it's own page and the purpose of the design should be to sell products (and some services as products). Please put a link or some other creative method to lead users to the About Us page if you must but not on the real estate of the page.

Thanks!

Added updates to the brief 7/14/2013.

Thanks!

The voting is in and the project is complete.  Thanks everyone for joining, all of those who participated are truly amazingly talented. But, there were only 3 prizes.  I will be having further projects down the line to develop other pages to this site after the initial implementation is completed.  I truly would like to have you all back. 

- Thank you.

Target Market(s)

corporate decision-makers AND small business consumers

Industry/Entity Type

Small Business

Requirements
Must have
• Call to action.
Openness (non-clutter).

These elements:
Search box
Logo
Tagline
Telephone number
Contact details
Address
My account / sign in
Shopping basket / checkout link
Latest offers
Promotional area
Email sign up
Delivery information
About us
Link to press office / corporate site
Terms and conditions
Sitemap for the footer.
Delivery offers: free
Personalized recommendations
Social media links
Accepted payment methods
Link to blog or community section
Change language / country

http://smartplansblog.pelloware.com/sales-leads-landing-page/

UPDATE 07/14/2013
Category Menu. This can be a dropdown, horizontal, vertical, etc. But shoppers need to know how to get to the products they want to buy.
Nice to have
• Trustmarks
Blog/Blog link

UPDATE 07/12/2013:
Make the footer useful.

UPDATE 07/14/2013 (Suggestions of elements to differentiate your designs)

-Quick Shop: A quick buy module/section: Where a user can put in a SKU number or Model number to quickly add the product to their shopping cart.

-Featured
-Best Sellers
-Specials
-Trending Tags/Tag Cloud
- Activity Stream
- Cross Sell/ Up Sell
- Testimonial
- Social Network Feed
- Live Help
- Feedback/Support/Contact Tab
- Show logged in user (i.e. Welcome, Mark Pelley)
Should not have
• The design SHOULD NOT be generic like this:

http://www.artgatherly.com/design/52392
http://www.falconmart.com/

The page should not feel over cluttered. It should not have low quality icons or design elements. Navigation should not be hard to discover or confusing.

```html
<!DOCTYPE html>
<html lang="en">
<head>
<meta charset="utf-8">
<title>Q.B. Brightpath Store – Home</title>
<link rel="stylesheet" href="https://fonts.googleapis.com/css2?family=Open+Sans:ital,wght@0,400;0,600;0,700;1,400;1,700&family=Source+Sans+3:wght@400;600;700&display=swap">
<style>
:root{
  --blue:#1a6db4;
  --blue-dark:#0f5a9c;
  --navy:#0b2374;
  --orange:#f7941d;
  --orange-dark:#e07d0c;
  --grey-nav:#cfcfcf;
  --grey-side:#5c5c5c;
  --grey-side-line:#6d6d6d;
  --grey-text:#666;
  --ink:#222;
  --line:#dcdcdc;
  --white:#fff;
  --tag:#9d9d9d;
}
*{box-sizing:border-box;margin:0;padding:0}
html,body{width:1200px;height:2310px;overflow:hidden;background:var(--white)}
body{font-family:"Open Sans",Arial,sans-serif;color:var(--ink)}
.canvas{position:relative;width:1200px;height:2310px;overflow:hidden}
.abs{position:absolute}
ul{list-style:none}

/* header */
.brand{left:162px;top:20px;display:flex;align-items:center;gap:12px}
.brand-dot{width:58px;height:58px;border-radius:50%;background:var(--blue)}
.brand-name{font-family:"Source Sans 3",sans-serif;font-weight:700;color:var(--blue);font-size:30px;line-height:28px;letter-spacing:1px}
.phone{left:585px;top:20px;display:flex;align-items:center;gap:8px;color:var(--blue);font-family:"Source Sans 3",sans-serif;font-size:22px;font-weight:600}
.top-links{left:748px;top:26px;display:flex;align-items:center;gap:9px;font-size:11px;font-weight:600;color:#333}
.top-links .signup{background:var(--orange);color:#fff;padding:1px 5px}
.cart-count{left:998px;top:18px;width:40px;height:34px;border-radius:50%;border:3px solid var(--blue);background:var(--navy);color:#fff;font-size:15px;font-weight:700;display:flex;align-items:center;justify-content:center}
.social-top{left:782px;top:60px;display:flex;gap:6px}
.social-dot{width:24px;height:24px;border-radius:50%;background:var(--blue)}
.search{left:880px;top:61px;width:158px;height:23px;border:1px solid #c9c9c9;border-radius:2px;font-size:10px;color:#999;padding:4px 6px}
.search svg{position:absolute;right:5px;top:5px}

/* nav */
.main-nav{left:0;top:106px;width:1200px;height:43px;background:var(--grey-nav)}
.main-nav ul{position:absolute;left:162px;top:0;display:flex;height:43px}
.main-nav li{color:#fff;font-size:16px;height:43px;line-height:43px;padding:0 18px 0 0;letter-spacing:.3px}
.main-nav li:first-child{padding-right:28px}
.main-nav li.active{background:var(--blue);padding:0 25px;margin-right:18px}

/* hero */
.hero{left:0;top:149px;width:1200px;height:400px;background:linear-gradient(90deg,#fff 0%,#fbfbfb 45%,#f0f0f0 100%)}
.hero-photo{position:absolute;left:640px;top:0;width:560px;height:400px;background:radial-gradient(ellipse at 62% 58%,#3a3a3a 0%,#7a7a7a 18%,#d8d8d8 40%,#f4f4f4 65%,rgba(255,255,255,0) 80%)}
.hero h1{position:absolute;left:166px;top:75px;font-family:"Source Sans 3",sans-serif;font-weight:700;color:var(--blue);font-size:40px;line-height:40px}
.hero p{position:absolute;left:166px;top:172px;width:500px;font-size:17px;line-height:21px;color:#333}
.price-old{position:absolute;left:166px;top:226px;font-size:20px;font-weight:700;color:#444;text-decoration:line-through}
.price-new{position:absolute;left:254px;top:222px;font-size:25px;font-weight:700;color:var(--blue)}
.btn{position:absolute;display:flex;align-items:center;justify-content:center;gap:14px;color:#fff;font-family:"Source Sans 3",sans-serif;font-weight:600;font-size:25px;border-radius:3px}
.btn-buy{left:160px;top:278px;width:178px;height:40px;background:linear-gradient(#fba33a,var(--orange-dark))}
.btn-touch{left:353px;top:278px;width:226px;height:40px;background:linear-gradient(#2b85cc,var(--blue-dark))}
.btn-icon{width:24px;height:24px;border-radius:50%;background:#fff}
.badge-offer{position:absolute;left:952px;top:33px;width:86px;height:86px}
.arrow{position:absolute;top:180px}
.feedback{left:0;top:267px;width:46px;height:111px;background:var(--blue);border-radius:0 4px 4px 0;color:#fff;font-weight:700;font-size:15px}
.feedback span{position:absolute;left:50%;top:50%;transform:translate(-50%,-50%) rotate(-90deg)}
.hero-rule{left:0;top:549px;width:1200px;height:4px;background:#e4e4e4}

/* sidebar */
.side-head{width:219px;height:42px;background:linear-gradient(#2f8ad2,var(--blue-dark));color:#fff;font-family:"Source Sans 3",sans-serif;font-size:19px;font-weight:600;padding:0 25px;line-height:42px;letter-spacing:.4px}
.cat-menu{left:162px;top:608px;width:219px}
.cat-menu li{height:30px;line-height:30px;font-size:12px;color:#fff;background:var(--grey-side);border-bottom:1px solid var(--grey-side-line);padding-left:10px}
.cat-menu li.open{background:var(--orange)}
.cat-menu li.sub{background:#f1f1f1;color:#333;padding-left:54px;border-bottom:1px solid #e3e3e3}
.cat-menu li.sub.current{background:#fff;color:var(--orange)}
.cat-menu li.sub:before{content:"";display:inline-block;width:5px;height:5px;background:#333;margin:0 8px 2px -14px}
.tags{left:162px;top:1000px;width:219px}
.tag-box{background:#e3e3e3;height:142px;padding:14px 20px;display:flex;flex-direction:column;gap:5px}
.tag-row{display:flex;gap:4px}
.tag{background:var(--tag);color:#fff;font-size:10px;height:17px;line-height:17px;text-align:center;white-space:nowrap}
.t42{width:42px}.t50{width:50px}.t78{width:78px}.t86{width:86px}
.ad-side{left:162px;top:1205px;width:219px;height:211px;border:1px solid #e2e2e2}
.ad-label{font-size:9px;color:#aaa;text-align:right}
.ad-side .ad-label{position:absolute;right:28px;top:4px}
.ad-art{position:absolute;left:24px;top:24px;width:167px;height:167px;background:linear-gradient(135deg,#6db33f,#3d8b24)}
.ad-art span{position:absolute;left:0;right:0;top:56px;text-align:center;color:#fff;font-family:"Source Sans 3",sans-serif;font-weight:700;font-size:20px;line-height:22px}
.social-tabs{left:162px;top:1443px;width:219px;height:32px;display:flex;font-size:13px}
.social-tabs div{flex:1;display:flex;align-items:center;gap:6px;padding-left:14px;border:1px solid #ddd}
.social-tabs .on{background:#fff;color:var(--blue);border-bottom:none}
.social-tabs .off{background:#d6d6d6;color:#444}
.sq{width:12px;height:12px;background:var(--blue)}
.social-tabs .off .sq{background:#444}
.fans{left:162px;top:1494px;width:219px;font-size:13px}
.fans h4{font-weight:600;font-size:13px;margin-left:3px;margin-bottom:10px}
.fan-page{display:flex;gap:8px;padding:10px 3px;border-top:1px solid #e5e5e5;border-bottom:1px solid #e5e5e5}
.fan-page .dot{width:36px;height:36px;border-radius:50%;background:var(--blue)}
.fan-page small{display:block;font-size:9px;color:#666}
.fan-page .like{display:inline-block;font-size:9px;border:1px solid #bbb;padding:0 4px;margin-top:3px;color:var(--blue)}
.fan-count{font-size:10px;margin:8px 3px}
.fan-count b{color:var(--blue);font-weight:400}
.fan-grid{display:grid;grid-template-columns:repeat(5,40px);gap:4px 4px;margin-left:3px}
.fan{font-size:9px;text-align:center;color:#333}
.fan i{display:block;width:40px;height:40px;background:linear-gradient(135deg,#9a8a7a,#5b5048);margin-bottom:2px}
.fan-foot{font-size:10px;margin:10px 3px 0;padding-top:6px;border-top:1px solid #e5e5e5;display:flex;gap:6px;align-items:center}
.fan-foot .sq{width:10px;height:10px}

/* products */
.section-title{font-family:"Source Sans 3",sans-serif;color:var(--blue);font-size:26px;font-weight:600;letter-spacing:.3px}
.featured-title{left:418px;top:604px}
.product-grid{left:418px;top:656px;width:620px;display:grid;grid-template-columns:repeat(3,190px);gap:24px 25px}
.product{position:relative;height:261px;border:1px solid #dcdcdc;border-radius:3px;background:#fff;box-shadow:0 1px 2px rgba(0,0,0,.08);text-align:center;overflow:hidden}
.product.highlight{border:2px solid var(--blue)}
.product-shot{position:absolute;left:25px;top:22px;width:140px;height:110px;background:linear-gradient(160deg,#f3f3f3 10%,#bfc7cf 45%,#2f3640 70%,#dfe3e7 90%);border-radius:6px}
.product-shot.dark{left:0;top:0;width:188px;height:130px;border-radius:0;background:linear-gradient(135deg,#2c2f35,#4f8fb0 55%,#22262b)}
.product h3{position:absolute;left:0;right:0;top:144px;font-family:"Source Sans 3",sans-serif;font-size:17px;font-weight:600}
.product p{position:absolute;left:22px;right:22px;top:172px;font-size:11px;line-height:16px;color:#444}
.product .price{position:absolute;left:15px;top:221px;font-size:17px;font-weight:600;color:var(--blue)}
.btn-small{display:inline-block;background:var(--orange);color:#fff;font-size:9px;height:15px;line-height:15px;padding:0 6px;text-align:center;white-space:nowrap}
.product .btn-small{position:absolute;left:93px;top:226px;width:78px}
.ribbon{position:absolute;left:0;top:0}

/* activity / testimonials / about */
.info-box{left:418px;top:1229px;width:620px;height:435px;border:1px solid #dcdcdc;border-radius:3px;box-shadow:0 1px 2px rgba(0,0,0,.08)}
.info-h{font-family:"Source Sans 3",sans-serif;font-size:18px;font-weight:700;color:var(--blue);letter-spacing:.3px;line-height:24px}
.activity{left:25px;top:33px;width:280px}
.activity .lead{font-size:14px;line-height:19px;color:#666;margin-top:10px}
.activity-photo{position:absolute;left:0;top:112px;width:80px;height:77px;background:linear-gradient(135deg,#c8302a,#e9b9a6 60%,#8a8a8a)}
.activity ul{position:absolute;left:92px;top:112px;font-size:12px;line-height:19px;color:#333}
.activity ul li:before{content:"› "}
.activity .btn-small{position:absolute;left:204px;top:193px;width:69px}
.testimonial{left:329px;top:33px;width:275px}
.testimonial-photo{position:absolute;left:0;top:34px;width:53px;height:53px;border-radius:50%;background:linear-gradient(#b7a08e,#6f5a4c)}
.testimonial .name{position:absolute;left:66px;top:38px;font-size:16px;font-weight:700}
.testimonial .place{position:absolute;left:66px;top:60px;font-size:13px;color:#999}
.testimonial blockquote{position:absolute;left:0;top:100px;width:275px;font-size:12px;line-height:18px;font-style:italic;font-weight:700;color:#333}
.testimonial .quote{position:absolute;left:0;top:176px;font-size:50px;line-height:50px;color:#b8c8d8;font-family:Georgia,serif}
.testimonial .btn-small{position:absolute;left:160px;top:193px;width:94px}
.about-rule{left:0;top:248px;width:618px;height:1px;background:#e3e3e3}
.about{left:25px;top:266px;width:580px}
.about .strong{margin-top:8px;font-size:13.5px;line-height:19px;font-weight:700;color:#444;letter-spacing:-.1px}
.about .body{font-size:11.6px;line-height:18px;color:#444}
.about .btn-small{position:absolute;right:4px;top:144px;width:72px}

/* banner ad */
.ad-banner-label{left:970px;top:1684px}
.ad-banner{left:424px;top:1698px;width:608px;height:75px;border:1px solid #ccc;background:linear-gradient(90deg,#fff 0%,#fff 60%,#e9e4cc 100%)}
.ad-banner .sponsor{position:absolute;left:12px;top:25px;display:flex;align-items:center;gap:5px;font-family:"Source Sans 3",sans-serif;font-weight:700;font-size:18px;color:var(--blue)}
.ad-banner .sponsor i{width:16px;height:16px;border-radius:50%;background:var(--blue)}
.ad-banner .pitch{position:absolute;left:150px;top:12px;width:200px;font-family:"Source Sans 3",sans-serif;font-weight:600;font-size:20px;line-height:24px;color:#222;text-align:center}
.ad-banner .art{position:absolute;left:362px;top:4px;width:240px;height:66px;background:linear-gradient(90deg,#f2e6a6,#c9d79e,#e9c47c)}

/* promo tiles */
.promo{top:1819px;height:101px;border-radius:3px;overflow:hidden;color:#fff}
.promo-1{left:162px;width:275px;background:linear-gradient(90deg,#2f4d7a 0%,#3e5d86 55%,#1c2a3f 100%)}
.promo-2{left:466px;width:276px;background:linear-gradient(90deg,#9b5a24 0%,#d68e45 55%,#8c6547 100%)}
.promo-3{left:762px;width:275px;background:linear-gradient(90deg,#2a73b3 0%,#3f8fcf 60%,#7fb5da 100%)}
.promo h4{position:absolute;left:25px;top:18px;font-family:"Source Sans 3",sans-serif;font-weight:700;font-size:20px;line-height:18px;letter-spacing:.2px}
.promo-3 h4{left:101px}
.promo .btn-small{position:absolute;left:25px;top:68px;width:78px}
.promo-3 .btn-small{left:101px}
.promo .pct{position:absolute;left:200px;top:20px;font-family:"Source Sans 3",sans-serif;font-weight:700;font-size:46px;line-height:46px}
.promo .pct small{display:block;font-size:13px;line-height:14px;background:rgba(255,255,255,.25);text-align:center;margin-top:2px}
.promo-3 svg{position:absolute;left:25px;top:24px}

/* footer */
.footer{left:0;top:1976px;width:1200px;height:280px;background:var(--navy);color:#fff}
.footer h5{position:absolute;top:58px;font-size:13px;font-weight:600;letter-spacing:.3px}
.footer .col-rule{position:absolute;top:81px;height:1px;background:#29408a}
.foot-list{position:absolute;top:94px;font-size:11px;line-height:22.4px}
.foot-list li:before{content:"";display:inline-block;width:6px;height:6px;background:#fff;margin-right:10px;vertical-align:1px}
.blog-post{position:absolute;left:413px;width:250px;height:50px}
.blog-post i{position:absolute;left:0;top:0;width:43px;height:43px;background:linear-gradient(135deg,#c9a58a,#7d6a5e)}
.blog-post b{position:absolute;left:56px;top:-2px;font-size:13px;color:var(--orange)}
.blog-post span{position:absolute;left:56px;top:16px;font-size:11px;white-space:nowrap}
.blog-post small{position:absolute;left:56px;top:31px;font-size:9px;color:#8ea0d0}
.newsletter-input{position:absolute;left:688px;top:94px;width:157px;height:23px;background:#fff;border-radius:2px;color:#555;font-size:10px;padding:5px 8px;display:flex;gap:5px;align-items:center}
.newsletter-input i{width:11px;height:8px;background:#888}
.newsletter-btn{position:absolute;left:688px;top:123px;width:157px;height:26px;background:var(--orange);border-radius:2px;font-size:13px;font-weight:700;text-align:center;line-height:26px}
.tollfree{position:absolute;left:872px;top:92px;display:flex;gap:8px;align-items:center}
.tollfree small{display:block;font-size:9px;font-weight:700}
.tollfree b{font-size:20px;font-weight:600;color:var(--orange);line-height:20px}
.social-foot{position:absolute;left:872px;top:130px;display:flex;gap:5px}
.social-foot i{width:24px;height:24px;border-radius:50%;background:#fff}
.foot-brand{position:absolute;left:872px;top:182px;display:flex;gap:7px;align-items:center}
.foot-brand i{width:30px;height:30px;border-radius:50%;background:#1e4aa8}
.foot-brand span{font-family:"Source Sans 3",sans-serif;font-weight:700;font-size:15px;line-height:14px}
.legal{left:162px;top:2275px;font-size:11px;color:#222}
.payments{left:813px;top:2271px;display:flex;gap:5px}
.payments i{width:41px;height:27px;border-radius:3px;border:1px solid #ccc;background:linear-gradient(#f7f7f7,#dfe5ee)}
</style>
</head>
<body>
<div class="canvas">

  <header>
    <a class="abs brand"><span class="brand-dot"></span><span class="brand-name">BRIGHTPATH<br>SOLUTIONS</span></a>
    <div class="abs phone">
      <svg width="24" height="24" viewBox="0 0 24 24"><circle cx="12" cy="12" r="11" fill="none" stroke="#1a6db4" stroke-width="2"/><path d="M8 6l2.5 0 1 3-1.5 1.2a7 7 0 0 0 3.8 3.8l1.2-1.5 3 1v2.5c0 .8-.7 1.5-1.5 1.5A10 10 0 0 1 6.5 7.5C6.5 6.7 7.2 6 8 6z" fill="#1a6db4"/></svg>
      555.312.7780
    </div>
    <nav class="abs top-links"><span>SIGNIN</span><span class="signup">SIGNUP</span><span>CHECKOUT</span><span>MY CART</span></nav>
    <div class="abs cart-count">12</div>
    <div class="abs social-top"><i class="social-dot"></i><i class="social-dot"></i><i class="social-dot"></i></div>
    <div class="abs search">Search
      <svg width="12" height="12" viewBox="0 0 12 12"><circle cx="5" cy="5" r="3.6" fill="none" stroke="#888" stroke-width="1.6"/><path d="M7.6 7.6l3 3" stroke="#888" stroke-width="1.8"/></svg>
    </div>
  </header>

  <nav class="abs main-nav">
    <ul>
      <li>HOME</li><li class="active">HARDWARE</li><li>LICENSING</li><li>MANAGEMENT</li><li>TECHNOLOGY SERVICES</li><li>BENEFITS</li><li>CONTACT</li>
    </ul>
  </nav>

  <section class="abs hero">
    <div class="hero-photo" role="img" aria-label="Black office headset with cushioned ear pad on a white background"></div>
    <h1>Luanch New Media Digital<br>Head Phone, Marketing</h1>
    <p>Lorem ipsum dolor sit amet, consec tetur adipisicing elit, sed eiusmod tempor incididunt ut labore...</p>
    <span class="price-old">$200.00</span>
    <span class="price-new">$150.00</span>
    <a class="btn btn-buy">Buy Now <i class="btn-icon"></i></a>
    <a class="btn btn-touch">Get In Touch <i class="btn-icon"></i></a>
    <svg class="badge-offer" viewBox="0 0 86 86">
      <polygon fill="#e3151a" points="43,0 50,8 60,3 63,13 74,12 73,23 83,27 78,36 86,43 78,50 83,59 73,63 74,74 63,73 60,83 50,78 43,86 36,78 26,83 23,73 12,74 13,63 3,59 8,50 0,43 8,36 3,27 13,23 12,12 23,13 26,3 36,8"/>
      <text x="43" y="39" fill="#fff" font-family="Open Sans, sans-serif" font-weight="700" font-size="14" text-anchor="middle">Special</text>
      <text x="43" y="57" fill="#fff" font-family="Open Sans, sans-serif" font-weight="700" font-size="14" text-anchor="middle">offer</text>
    </svg>
    <svg class="arrow" style="left:108px" width="20" height="36" viewBox="0 0 20 36"><path d="M17 3L4 18l13 15" fill="none" stroke="#bbb" stroke-width="5"/></svg>
    <svg class="arrow" style="left:1072px" width="20" height="36" viewBox="0 0 20 36"><path d="M3 3l13 15L3 33" fill="none" stroke="#ddd" stroke-width="5"/></svg>
  </section>
  <div class="abs feedback"><span>Feedback</span></div>
  <div class="abs hero-rule"></div>

  <aside>
    <div class="abs cat-menu">
      <div class="side-head">MANUFACTURES</div>
      <ul>
        <li>+&nbsp; Dummy lorem ipsume</li>
        <li class="open">–&nbsp; Lorem ipsume categories</li>
        <li class="sub">A-Z Directory</li>
        <li class="sub current">Authorization</li>
        <li class="sub">New Manufactures</li>
        <li class="sub">Stores</li>
        <li>+&nbsp; Dummy product categories</li>
        <li>+&nbsp; Dummy lorem ipsume</li>
        <li>+&nbsp; Lorem ipsume categories</li>
        <li>+&nbsp; Dummy product categories</li>
      </ul>
    </div>

    <div class="abs tags">
      <div class="side-head">TRENDING TAGS</div>
      <div class="tag-box">
        <div class="tag-row"><span class="tag t42">Lorem</span><span class="tag t78">Dummy Tag</span><span class="tag t50">Ipsum</span></div>
        <div class="tag-row"><span class="tag t78">Dummy Tag</span><span class="tag t42">Lorem</span><span class="tag t50">Ipsum</span></div>
        <div class="tag-row"><span class="tag t42">Ipsum</span><span class="tag t42">Lorem</span><span class="tag t86">Dummy Tag</span></div>
        <div class="tag-row"><span class="tag t78">Dummy Tag</span><span class="tag t42">Ipsum</span><span class="tag t50">Lorem</span></div>
        <div class="tag-row"><span class="tag t42">Lorem</span><span class="tag t78">Dummy Tag</span><span class="tag t50">Ipsum</span></div>
      </div>
    </div>

    <div class="abs ad-side">
      <span class="ad-label">Advertisement</span>
      <div class="ad-art" role="img" aria-label="Green advertisement badge for a store builder, 30 day free trial"><span>CREATE YOUR OWN<br>ONLINE STORE</span></div>
    </div>

    <div class="abs social-tabs">
      <div class="on"><i class="sq"></i>Friendbook</div>
      <div class="off"><i class="sq"></i>Chirper</div>
    </div>
    <div class="abs fans">
      <h4>Find us on Friendbook</h4>
      <div class="fan-page"><i class="dot"></i><div><small>Brightpath Solutions</small><span class="like">Like</span></div></div>
      <p class="fan-count">10,895 people like <b>BrightpathSolutions</b></p>
      <div class="fan-grid">
        <div class="fan"><i role="img" aria-label="Fan profile photo"></i>Lorem</div>
        <div class="fan"><i role="img" aria-label="Fan profile photo"></i>Ipsum</div>
        <div class="fan"><i role="img" aria-label="Fan profile photo"></i>Doe</div>
        <div class="fan"><i role="img" aria-label="Fan profile photo"></i>Stephen</div>
        <div class="fan"><i role="img" aria-label="Fan profile photo"></i>Dummy</div>
        <div class="fan"><i role="img" aria-label="Fan profile photo"></i>Lorem</div>
        <div class="fan"><i role="img" aria-label="Fan profile photo"></i>Ipsum</div>
        <div class="fan"><i role="img" aria-label="Fan profile photo"></i>Doe</div>
        <div class="fan"><i role="img" aria-label="Fan profile photo"></i>Stephen</div>
        <div class="fan"><i role="img" aria-label="Fan profile photo"></i>Dummy</div>
      </div>
      <p class="fan-foot"><i class="sq"></i>Friendbook social Plug</p>
    </div>
  </aside>

  <h2 class="abs section-title featured-title">FEATURED PRODUCTS</h2>
  <div class="abs product-grid">
    <article class="product highlight">
      <div class="product-shot" role="img" aria-label="Two smartphones, black and white"></div>
      <svg class="ribbon" width="44" height="44" viewBox="0 0 44 44"><path d="M0 0h44L0 44z" fill="#d9151b"/><text x="9" y="24" transform="rotate(-45 15 18)" fill="#fff" font-size="10" font-weight="700" font-family="Open Sans, sans-serif">New</text></svg>
      <h3>Product Title</h3><p>Lorem ipsum dolor sit amet, consec</p>
      <span class="price">$150.00</span><span class="btn-small">More Details</span>
    </article>
    <article class="product">
      <div class="product-shot" role="img" aria-label="Black smartphone beside a white smartphone"></div>
      <svg class="ribbon" width="44" height="44" viewBox="0 0 44 44"><path d="M0 0h44L0 44z" fill="#3d7f26"/><text x="10" y="24" transform="rotate(-45 15 18)" fill="#fff" font-size="10" font-weight="700" font-family="Open Sans, sans-serif">Sold</text></svg>
      <h3>Product Title</h3><p>Lorem ipsum dolor sit amet, consec</p>
      <span class="price">$150.00</span><span class="btn-small">More Details</span>
    </article>
    <article class="product">
      <div class="product-shot" role="img" aria-label="White smartphone lying flat"></div>
      <h3>Product Title</h3><p>Lorem ipsum dolor sit amet, consec</p>
      <span class="price">$150.00</span><span class="btn-small">More Details</span>
    </article>
    <article class="product">
      <div class="product-shot" role="img" aria-label="Two smartphones, front and back"></div>
      <h3>Product Title</h3><p>Lorem ipsum dolor sit amet, consec</p>
      <span class="price">$150.00</span><span class="btn-small">More Details</span>
    </article>
    <article class="product">
      <div class="product-shot" role="img" aria-label="White smartphone side view"></div>
      <h3>Product Title</h3><p>Lorem ipsum dolor sit amet, consec</p>
      <span class="price">$150.00</span><span class="btn-small">More Details</span>
    </article>
    <article class="product">
      <div class="product-shot dark" role="img" aria-label="Smartphone resting on a laptop keyboard"></div>
      <h3>Product Title</h3><p>Lorem ipsum dolor sit amet, consec</p>
      <span class="price">$150.00</span><span class="btn-small">More Details</span>
    </article>
  </div>

  <section class="abs info-box">
    <div class="abs activity">
      <h3 class="info-h">ACTIVITY STREAM</h3>
      <p class="lead">Lorem ipsum dolor sit amet, consec tetur cing elit, sed do eiusmod et dolore</p>
      <div class="activity-photo" role="img" aria-label="Red sports car"></div>
      <ul>
        <li>Eaque ipsa quae ab illo</li>
        <li>Lorem ipsum dolor sit amet</li>
        <li>High quality sales leads</li>
        <li>Excepteur sint occaecat</li>
      </ul>
      <span class="btn-small">Learn More</span>
    </div>
    <div class="abs testimonial">
      <h3 class="info-h">TESTIMONIALS</h3>
      <div class="testimonial-photo" role="img" aria-label="Customer portrait"></div>
      <span class="name">Paul Ransom</span>
      <span class="place">New York, USA</span>
      <blockquote>Lorem ipsum dolor sit amet, consec tetur cing elit, sed do eiusmod et dolore tempor ut labore et dolore magna aliqua. Ut enim ad minim veniam, nostrud labore citation ullamco</blockquote>
      <span class="quote">“</span>
      <span class="btn-small">All Testimonials</span>
    </div>
    <div class="abs about-rule"></div>
    <div class="abs about">
      <h3 class="info-h">ABOUT US</h3>
      <p class="strong">Lorem ipsum dolor sit amet, consectetur adipisicing elit, do eiusmod tempor incididunt ut labore et dolore magna aliqua. Ut enim ad minim veniam,</p>
      <p class="body">quis nostrud exercitation ullamco laboris nisi ut aliquip ex ea commodo consequat. Duis aute irure dolor in reprehenderit in voluptate velit esse cillum dolore eu fugiat nulla pariatur. Excepteur sint occaecat cupidatat non proident, sunt in culpa qui officia deserunt mollit anim ...</p>
      <span class="btn-small">Learn More</span>
    </div>
  </section>

  <span class="abs ad-label ad-banner-label">Advertisement</span>
  <div class="abs ad-banner">
    <span class="sponsor"><i></i>Textwire</span>
    <span class="pitch">Who uses our<br>messaging APIs?</span>
    <div class="art" role="img" aria-label="Cartoon line-up of programming language mascots"></div>
  </div>

  <div class="abs promo promo-1" role="img" aria-label="Headset product shot, best seller promotion">
    <h4>BEST SELLER<br>OF THIS MONTH</h4><span class="btn-small">More Details</span>
  </div>
  <div class="abs promo promo-2" role="img" aria-label="Hands on a keyboard, special offer promotion">
    <h4>SPECIAL OFFER<br>OF THIS MONTH</h4><span class="pct">20%<small>DISCOUNT</small></span><span class="btn-small">More Details</span>
  </div>
  <div class="abs promo promo-3" role="img" aria-label="Free shipping promotion">
    <svg width="60" height="52" viewBox="0 0 60 52"><path d="M4 28l16 18L56 4" fill="none" stroke="#fff" stroke-width="9" stroke-linecap="round" stroke-linejoin="round"/></svg>
    <h4>FREE SHIPPING<br>ON EVERY ORDER</h4><span class="btn-small">More Details</span>
  </div>

  <footer class="abs footer">
    <h5 style="left:163px">ABOUT US</h5>
    <h5 style="left:272px">POPULAR SALES</h5>
    <h5 style="left:413px">LATEST BLOG POSTS</h5>
    <h5 style="left:688px">NEWSLETTER SIGNUP</h5>
    <h5 style="left:872px">CONTACT US</h5>
    <span class="col-rule" style="left:163px;width:90px"></span>
    <span class="col-rule" style="left:272px;width:120px"></span>
    <span class="col-rule" style="left:413px;width:255px"></span>
    <span class="col-rule" style="left:688px;width:160px"></span>
    <span class="col-rule" style="left:872px;width:170px"></span>
    <ul class="foot-list" style="left:163px"><li>Home</li><li>Hardware</li><li>Software</li><li>Services</li><li>Contact</li></ul>
    <ul class="foot-list" style="left:272px"><li>Lorem Ipsum</li><li>Dummy Product</li><li>Standard lorem</li><li>Lorem Ipsum</li><li>Dummy Product</li><li>Standard lorem</li></ul>
    <div class="blog-post" style="top:93px"><i role="img" aria-label="Blog post thumbnail"></i><b>Consectetur adipisicing elit</b><span>Lorem ipsum dolor sit consectetur...</span><small>Julu 16, 2013</small></div>
    <div class="blog-post" style="top:156px"><i role="img" aria-label="Blog post thumbnail"></i><b>Consectetur adipisicing elit</b><span>Lorem ipsum dolor sit consectetur...</span><small>Julu 16, 2013</small></div>
    <div class="newsletter-input"><i></i>Enter Email</div>
    <div class="newsletter-btn">Subscribe Now</div>
    <div class="tollfree">
      <svg width="22" height="22" viewBox="0 0 24 24"><path d="M6 2l4 0 1.5 4.5-2.2 1.8a10 10 0 0 0 6.4 6.4l1.8-2.2L22 14v4c0 1.2-1 2-2 2A18 18 0 0 1 4 4c0-1 .8-2 2-2z" fill="#fff"/></svg>
      <div><small>TOLLFREE</small><b>0800 55 01 987</b></div>
    </div>
    <div class="social-foot"><i></i><i></i><i></i><i></i></div>
    <div class="foot-brand"><i></i><span>BRIGHTPATH<br>SOLUTIONS</span></div>
  </footer>

  <p class="abs legal">Copyright © 2013, QBBrightpathSolutions.com, All Rights Reserved.</p>
  <div class="abs payments" role="img" aria-label="Accepted payment methods"><i></i><i></i><i></i><i></i><i></i></div>

</div>
</body>
</html>
```